Finding the Root: Reason in Clinical Choice-Crafting

I'd like a cover that looks like it would fit on the shelf next to "The Illness Mirage" by Corwin Talley, "The Close of Forgetting" by Hugh Marchetti, "Meal Mend" by Paul Grieve, "The Energy Restart Plan" by Oscar Pemberley or "The Gland Restart Plan" by the same or "The Cortex Restart Plan" by the same ... either text only (with some interesting fonts that make the title stand out, and the subtitle smaller) or a relevant image, though I'm not entirely sure what that would be since this is a book about big-picture medical decision making.
Author name is Dr Tessa Morrow, NMD
I'll eventually request an e-book, paperback, and audio cover from the winner...

Target Market(s)

practicing physicians

Industry/Entity Type

medicine

Requirements
Must have
• look similar to other books in the genre

```html
<!DOCTYPE html>
<html lang="en">
<head>
<meta charset="utf-8">
<title>Finding the Root — Book Cover</title>
<link href="https://fonts.googleapis.com/css2?family=Oswald:wght@600&family=Playfair+Display:wght@500&family=Cinzel:wght@600&family=Libre+Caslon+Text&family=Montserrat:wght@600&display=swap" rel="stylesheet">
<style>
  :root {
    --backdrop: #9a9a9a;
    --paper: #f9f7f1;
    --navy: #0f2346;
    --green: #5d7236;
    --gold: #c08a2e;
    --wash-green: #b9c8a0;
    --wash-blue: #9fb5c9;
  }
  * { margin: 0; padding: 0; box-sizing: border-box; }
  html, body { width: 1200px; height: 1200px; overflow: hidden; background: var(--backdrop); }
  .cover {
    position: absolute; left: 268px; top: 102px;
    width: 663px; height: 996px;
    background: var(--paper);
    color: var(--navy);
  }
  .rules { position: absolute; inset: 0; width: 663px; height: 996px; }
  .line { position: absolute; left: 0; width: 100%; text-align: center; line-height: 1; white-space: nowrap; }
  .tagline {
    font-family: "Libre Caslon Text", Georgia, serif;
    font-size: 16px; line-height: 25px; top: 32px;
  }
  .title-top {
    font-family: "Oswald", "Arial Narrow", sans-serif; font-weight: 600;
    font-size: 132px; letter-spacing: 2px; top: 112px;
    transform: scaleX(0.78);
  }
  .title-main {
    font-family: "Playfair Display", Georgia, serif; font-weight: 500;
    color: var(--green); font-size: 232px; top: 238px; letter-spacing: -4px;
  }
  .subtitle-lead {
    font-family: "Montserrat", Arial, sans-serif; font-weight: 600;
    font-size: 21px; letter-spacing: 6px; top: 471px;
  }
  .subtitle-key {
    font-family: "Libre Caslon Text", Georgia, serif;
    color: var(--green); font-size: 42px; letter-spacing: 9px; top: 498px;
  }
  .subtitle-tail {
    font-family: "Montserrat", Arial, sans-serif; font-weight: 600;
    font-size: 22px; letter-spacing: 4px; top: 549px;
  }
  .compass-art {
    position: absolute; left: 124px; top: 612px; width: 422px; height: 255px;
    background:
      radial-gradient(circle at 50% 42%, #f2efe4 0 34%, #233a5c 35% 38%, transparent 39%),
      radial-gradient(ellipse at 30% 50%, var(--wash-green) 0%, transparent 55%),
      radial-gradient(ellipse at 72% 45%, var(--wash-blue) 0%, transparent 55%);
  }
  .label {
    position: absolute; font-family: "Montserrat", Arial, sans-serif; font-weight: 600;
    font-size: 12.5px; letter-spacing: 1px; line-height: 17px; text-align: center;
  }
  .label-questions { left: 62px; top: 694px; }
  .label-decisions { left: 522px; top: 697px; }
  .label-outcomes { left: 0; width: 664px; top: 866px; }
  .author {
    font-family: "Cinzel", Georgia, serif; font-weight: 600;
    font-size: 28px; letter-spacing: 3px; top: 917px;
  }
</style>
</head>
<body>
  <main class="cover">
    <svg class="rules" viewBox="0 0 663 996" aria-hidden="true">
      <g stroke="var(--gold)" stroke-width="1.4">
        <line x1="163" y1="104" x2="291" y2="104"/>
        <line x1="367" y1="104" x2="497" y2="104"/>
        <line x1="164" y1="481" x2="229" y2="481"/>
        <line x1="408" y1="481" x2="433" y2="481"/>
        <line x1="193" y1="589" x2="472" y2="589"/>
        <line x1="94" y1="904" x2="573" y2="904"/>
        <line x1="94" y1="945" x2="573" y2="945"/>
      </g>
      <g fill="var(--gold)">
        <circle cx="310" cy="104" r="3"/>
        <circle cx="329" cy="104" r="3"/>
        <circle cx="348" cy="104" r="3"/>
      </g>
      <g stroke="var(--navy)" stroke-width="1.2" fill="var(--navy)">
        <line x1="153" y1="712" x2="220" y2="712"/>
        <circle cx="153" cy="712" r="3"/>
        <line x1="443" y1="712" x2="518" y2="712"/>
        <circle cx="518" cy="712" r="3"/>
        <line x1="330" y1="830" x2="330" y2="859"/>
        <circle cx="330" cy="859" r="3"/>
      </g>
    </svg>

    <p class="line tagline">Asking the right questions<br>is the first step to getting the right answers.</p>

    <h1 class="title">
      <span class="line title-top">FINDING THE</span>
      <span class="line title-main">Root</span>
    </h1>

    <h2 class="subtitle">
      <span class="line subtitle-lead">REASON IN</span>
      <span class="line subtitle-key">CLINICAL</span>
      <span class="line subtitle-tail">CHOICE-CRAFTING</span>
    </h2>

    <div class="compass-art" role="img" aria-label="Brass navigation compass on a green and blue watercolour wash"></div>

    <p class="label label-questions">BETTER<br>QUESTIONS</p>
    <p class="label label-decisions">BETTER<br>DECISIONS</p>
    <p class="label label-outcomes">BETTER OUTCOMES</p>

    <p class="line author">DR TESSA MORROW, NMD</p>
  </main>
</body>
</html>
```